Wix Design for a Clothing Design Web Marketing Site

We need a Wix design and content (including any images and copy) for a clothing design web storefront, Sew To Suit (or sewtosuit). Rough ideas and content can be found at http://marenvoltis.wix.com/sewtosuit.

Sew To Suit is an innovative business concept that combines fashion and entertainment. The business model allows customers to actively participate in the creation of fashion designs/concepts , visualize the garment in the customer’s body in 3D, and buy the physical garment made specially to fit the customer.
The fashion consultant will be able to create the design based on client's desires and test various possibilities (size, fabric, cut, etc..) in front of the customer, using software Drapova (the software is a key component of this business model)
(when developing the website use images from Drapova)
After the design is created, the customer can choose to order the actual piece. The garment will be made according to the created design, the customer measurements.

Target Market(s)

Primarily women from 25 to 45, who are fashion enthusiasts and appreciate fit and exclusivity. They are hedonistic shoppers, who shop for entertainment.
Men (metrosexuals) who are fashion enthusiasts, also hedonistic shoppers.

Industry/Entity Type

Clothing

Font styles to use
Serif
Sans Serif

Requirements
Must have
• Must have a landing page (home) or section, that gives the consumer an idea of what Sew To Suit will do for them, an about page or section that tells about the company and product, a how it works page or section that describes how it works (http://marenvoltis.wix.com/sewtosuit#!services3/c192y), and page or section about pricing, and a page or section on how to contact us.
Nice to have
• Very modern and clean. The website must be based on the main picture of the studio in the example. If that studio is the store, what will the website look like?
• Colors yellow, grey and white. Use the zig zag in yellow and white. You can change the size of the lines. The zig zagi gives the modern and bold accent. Outfits in pictures must show nicely tailored garments.

```html
<!DOCTYPE html>
<html lang="en">
<head>
<meta charset="utf-8">
<title>Sew To Suit</title>
<link rel="stylesheet" href="https://fonts.googleapis.com/css2?family=Montserrat:wght@400;600;700&family=Playfair+Display+SC:wght@400;700&family=Oswald:wght@400;500&display=swap">
<style>
:root{
  --yellow:#f2d600;
  --yellow-pale:#fbf3a0;
  --olive:#b8b400;
  --ink:#1a1a1a;
  --line:#d9d9d9;
  --paper:#ffffff;
  --header-bg:#f2f2f2;
  --black:#0c0c0c;
}
*{box-sizing:border-box;margin:0;padding:0}
html,body{width:1200px;height:2400px;overflow:hidden}
body{position:relative;font-family:Arial,Helvetica,sans-serif;color:var(--ink);background:var(--yellow-pale)}
.backdrop{position:absolute;inset:0;background:linear-gradient(90deg,var(--yellow-pale),#fff8c4 50%,var(--yellow-pale))}
.page{position:absolute;left:100px;top:0;width:1000px;height:2400px;background:var(--paper)}
.abs{position:absolute}

/* header */
.site-header{position:absolute;left:0;top:0;width:1000px;height:171px;background:linear-gradient(#f7f7f7,var(--header-bg))}
.brand{left:20px;top:70px;display:flex;align-items:center;gap:10px}
.brand-square{width:20px;height:20px;background:var(--yellow)}
.brand-name{font:600 24px/1 Montserrat,sans-serif;color:var(--ink)}
.cart{left:795px;top:38px;display:flex;gap:10px;align-items:flex-start}
.cart-label{font:700 13px/1.2 Arial,sans-serif}
.cart-total{font:700 19px/1.2 Arial,sans-serif}
.search{left:709px;top:99px;width:271px;height:40px;border:1px solid #bbb;border-radius:3px;background:#fff;font-size:12px;color:#666;padding:0 12px;display:flex;align-items:center;justify-content:space-between}

/* nav */
.main-nav{position:absolute;left:0;top:171px;width:1000px;height:47px;border-top:1px solid var(--line);border-bottom:1px solid var(--line);background:#fff;display:flex}
.main-nav a{font:600 13px/45px Montserrat,sans-serif;color:var(--ink);text-decoration:none;border-right:1px solid var(--line);text-align:center}
.main-nav .home{width:132px;text-align:left;padding-left:23px}
.main-nav .home::after{content:"";display:inline-block;margin-left:14px;border:6px solid transparent;border-top:7px solid var(--yellow);vertical-align:-3px}

/* hero */
.hero{position:absolute;left:0;top:218px;width:1000px;height:422px;background:linear-gradient(90deg,#f0f0f0,#fafafa 60%,#f1f1f1)}
.hero-photo{left:0;top:0;width:443px;height:422px;background:linear-gradient(120deg,#d9d4cf,#b98f7a 45%,#c9c2bb)}
.hero-copy{left:440px;top:30px;width:560px;text-align:center}
.hero-kicker{font:700 46px/1 "Playfair Display SC",serif;color:var(--ink);letter-spacing:1px}
.hero-kicker .amp{color:var(--yellow);font-size:64px;font-weight:400;vertical-align:-4px}
.hero-title{font:400 122px/0.85 "Playfair Display SC",serif;color:var(--yellow);letter-spacing:1px}
.hero-sub{font:600 32px/1 Montserrat,sans-serif;color:var(--yellow);letter-spacing:3px;margin-top:22px}
.hero-season{width:396px;margin:28px auto 0;border-top:2px solid var(--ink);border-bottom:2px solid var(--ink);padding:12px 0;font:600 22px/1 Montserrat,sans-serif;letter-spacing:1px}
.btn-shop{display:inline-block;margin-top:22px;background:var(--yellow);color:#fff;font:700 17px/38px Montserrat,sans-serif;padding:0 18px}

/* intro */
.intro-title{left:0;top:662px;width:1000px;text-align:center;font:600 31px/1.3 Montserrat,sans-serif}
.intro-text{left:30px;top:714px;width:940px;text-align:center;font:14px/1.6 Arial,sans-serif;color:#222}
.tile{top:781px;width:305px;height:216px;overflow:hidden}
.tile-photo{position:absolute;inset:0}
.tile-caption{position:absolute;left:0;bottom:16px;width:275px;height:62px;background:rgba(30,22,16,.85);color:#fff;text-align:center}
.tile-caption small{display:block;font:700 10px/1 Montserrat,sans-serif;letter-spacing:1px;padding-top:12px}
.tile-caption strong{display:block;font:700 25px/1.2 "Playfair Display SC",serif}

/* products */
.section-title{left:0;width:1000px;text-align:center;font:600 31px/1.3 Montserrat,sans-serif}
.product{width:221px;height:322px;border:1px solid var(--line);background:#fff}
.product-photo{position:absolute;left:10px;top:10px;width:200px;height:246px}
.product-name{position:absolute;left:10px;top:268px;font:14px/1 Arial,sans-serif;color:#333}
.product-price{position:absolute;left:10px;top:292px;font:700 12px/1 Arial,sans-serif;color:var(--olive)}
.product-price s{text-decoration:none;color:#888;font-weight:400;margin-left:12px}
.product-cart{position:absolute;right:10px;top:274px;width:34px;height:34px;border-radius:50%;background:var(--olive)}

/* promo */
.promo{left:21px;top:1816px;width:937px;height:293px;border:1px dashed #8a6d5a;background:var(--black)}
.promo-photos{position:absolute;left:0;top:0;width:526px;height:291px;display:flex}
.promo-photos div{flex:1}
.promo-copy{position:absolute;left:526px;top:0;width:409px;height:291px;text-align:center;color:#fff;background:radial-gradient(#222,#0a0a0a)}
.promo-copy h2{font:700 46px/1 "Playfair Display SC",serif;color:var(--yellow);margin-top:28px;letter-spacing:1px}
.promo-copy p{font:400 30px/1 "Playfair Display SC",serif;margin-top:8px;letter-spacing:1px}
.promo-figure{font:400 150px/1 Montserrat,sans-serif;margin-top:6px;display:inline-block;position:relative}
.promo-figure sup{position:absolute;right:-42px;top:32px;font:600 28px/1 Montserrat,sans-serif;text-align:center}
.promo-figure sup small{display:block;font-size:11px}

/* footer */
.site-footer{position:absolute;left:0;top:2144px;width:1000px;height:256px;background:var(--black);color:#bbb}
.foot-col{position:absolute;top:32px}
.foot-col h3{font:500 14px/1 Oswald,sans-serif;color:var(--yellow);margin-bottom:16px;display:flex;align-items:center;gap:8px;text-transform:uppercase}
.foot-col h3 i{width:13px;height:13px;border-radius:50%;background:var(--yellow);display:inline-block}
.foot-col li{list-style:none;font:13px/22px Arial,sans-serif}
.social{position:absolute;left:616px;top:20px;width:362px;display:flex;align-items:center;gap:13px}
.social hr{flex:1;border:0;border-top:1px solid #444}
.social span{width:40px;height:40px;border-radius:50%}
.news-title{position:absolute;left:616px;top:88px;width:362px;text-align:center;font:400 18px/1 Oswald,sans-serif;color:var(--yellow)}
.news-text{position:absolute;left:616px;top:116px;width:362px;text-align:center;font:12px/1 Arial,sans-serif;color:#aaa}
.news-form{position:absolute;left:620px;top:136px;width:336px;height:44px;display:flex}
.news-input{flex:1;background:#fff;color:#888;font:13px/44px Arial,sans-serif;padding-left:14px}
.news-btn{width:48px;background:#5b3f78;display:flex;align-items:center;justify-content:center}
.foot-bar{position:absolute;left:0;top:208px;width:1000px;height:48px;border-top:1px solid #2a2a2a;font:13px/48px Arial,sans-serif;color:#aaa}
.foot-bar .copy{position:absolute;left:28px}
.foot-bar .legal{position:absolute;right:42px}
</style>
</head>
<body>
<div class="backdrop" role="img" aria-label="Yellow and white zigzag background pattern"></div>

<main class="page">
  <header class="site-header">
    <div class="abs brand"><span class="brand-square"></span><span class="brand-name">Sew To Suit</span></div>
    <div class="abs cart">
      <svg width="42" height="38" viewBox="0 0 42 38" aria-hidden="true"><path d="M2 4h7l5 20h22l4-14H12" fill="none" stroke="#c8161d" stroke-width="3"/><circle cx="16" cy="32" r="3.5" fill="#333"/><circle cx="33" cy="32" r="3.5" fill="#333"/></svg>
      <div><div class="cart-label">SHOPPING CART :</div><div class="cart-total">item(0) - $0.00</div></div>
    </div>
    <div class="abs search"><span>Search</span>
      <svg width="26" height="24" viewBox="0 0 26 24" aria-hidden="true"><circle cx="10" cy="10" r="7" fill="none" stroke="#555" stroke-width="2.5"/><path d="M15 15l8 7" stroke="#555" stroke-width="3"/></svg>
    </div>
  </header>

  <nav class="main-nav">
    <a class="home">HOME</a>
    <a style="width:216px">What Is Sew To Suit?</a>
    <a style="width:186px">How It works</a>
    <a style="width:121px">Price</a>
    <a style="width:179px">Contact Us</a>
  </nav>

  <section class="hero">
    <div class="abs hero-photo" role="img" aria-label="Model in an embroidered sheer sari in a bright studio"></div>
    <div class="abs hero-copy">
      <div class="hero-kicker">FREEDOM <span class="amp">&amp;</span></div>
      <div class="hero-title">FASHION</div>
      <div class="hero-sub">WOMAN COLLACTION</div>
      <div class="hero-season">SPRING SUMMER 2014</div>
      <span class="btn-shop">SHOP NOW</span>
    </div>
  </section>

  <h1 class="abs intro-title">What is Sew To Suit?</h1>
  <p class="abs intro-text">Sew To Suit is an innovative business concept that combines fashion and entertainment. Our services allow you to actively participate in the creation of fashion designs/concepts , visualize the garment in 3D, and buy the physical garment made specially to fit you.</p>

  <a class="abs tile" style="left:19px">
    <div class="tile-photo" role="img" aria-label="Model in a red knit sweater with accessories" style="background:linear-gradient(135deg,#b8323a,#6e1e24 55%,#2a1a14)"></div>
    <div class="tile-caption"><small>BROWSE FASHION</small><strong>ACCESSORIES</strong></div>
  </a>
  <a class="abs tile" style="left:347px">
    <div class="tile-photo" role="img" aria-label="Blonde model in a black top" style="background:linear-gradient(135deg,#e8e2da,#c9b9a6 50%,#2a2522)"></div>
    <div class="tile-caption"><small>BROWSE THE</small><strong>LATEST TRENDS</strong></div>
  </a>
  <a class="abs tile" style="left:677px">
    <div class="tile-photo" role="img" aria-label="Model sitting by a pool in summer wear" style="background:linear-gradient(135deg,#2aa6c8,#7fd0e6 50%,#d8d0c8)"></div>
    <div class="tile-caption"><small>SHOP</small><strong>SUMMER'S BEST</strong></div>
  </a>

  <h2 class="abs section-title" style="top:1046px">Featured Products</h2>

  <article class="abs product" style="left:22px;top:1102px"><div class="product-photo" role="img" aria-label="Black vest over red sleeves" style="background:linear-gradient(#e4e4e4,#3a2a2a 50%,#d8d8d8)"></div><div class="product-name">Maison Tailleur</div><div class="product-price">$ 1.180.46<s>$1.300</s></div><span class="product-cart"></span></article>
  <article class="abs product" style="left:266px;top:1102px"><div class="product-photo" role="img" aria-label="Camel coat with red trousers" style="background:linear-gradient(#ececec,#c8a984 45%,#c62b2b 80%,#e6e6e6)"></div><div class="product-name">Maison Tailleur</div><div class="product-price">$ 1.180.46<s>$1.300</s></div><span class="product-cart"></span></article>
  <article class="abs product" style="left:508px;top:1102px"><div class="product-photo" role="img" aria-label="Black jacket with brown trousers" style="background:linear-gradient(#ececec,#2a2626 45%,#5a3a30 80%,#e6e6e6)"></div><div class="product-name">Maison Tailleur</div><div class="product-price">$ 1.180.46<s>$1.300</s></div><span class="product-cart"></span></article>
  <article class="abs product" style="left:751px;top:1102px"><div class="product-photo" role="img" aria-label="Pink polo shirt with green trousers" style="background:linear-gradient(#dfe6ea,#e0356c 50%,#4caf50 95%)"></div><div class="product-name">Maison Tailleur</div><div class="product-price">$ 1.180.46<s>$1.300</s></div><span class="product-cart"></span></article>

  <article class="abs product" style="left:19px;top:1445px"><div class="product-photo" role="img" aria-label="Patterned print dress" style="background:linear-gradient(#ececec,#6e6258 50%,#e6e6e6)"></div><div class="product-name">Maison Tailleur</div><div class="product-price">$ 1.180.46<s>$1.300</s></div><span class="product-cart"></span></article>
  <article class="abs product" style="left:262px;top:1445px"><div class="product-photo" role="img" aria-label="Black jacket with brown trousers and bag" style="background:linear-gradient(#ececec,#2a2626 45%,#5a3a30 80%,#e6e6e6)"></div><div class="product-name">Maison Tailleur</div><div class="product-price">$ 1.180.46<s>$1.300</s></div><span class="product-cart"></span></article>
  <article class="abs product" style="left:505px;top:1445px"><div class="product-photo" role="img" aria-label="Red duffle coat" style="background:linear-gradient(#ececec,#d6322b 50%,#e6e6e6)"></div><div class="product-name">Maison Tailleur</div><div class="product-price">$ 1.180.46<s>$1.300</s></div><span class="product-cart"></span></article>
  <article class="abs product" style="left:748px;top:1445px"><div class="product-photo" role="img" aria-label="Black leather jacket and trousers" style="background:linear-gradient(#ececec,#1e1e1e 50%,#e6e6e6)"></div><div class="product-name">Maison Tailleur</div><div class="product-price">$ 1.180.46<s>$1.300</s></div><span class="product-cart"></span></article>

  <section class="abs promo">
    <div class="promo-photos">
      <div role="img" aria-label="Model in olive tunic outdoors" style="background:linear-gradient(#6b8a4a,#a8a07a)"></div>
      <div role="img" aria-label="Blonde model in a black dress" style="background:linear-gradient(#f4f2ee,#2a2624 70%)"></div>
      <div role="img" aria-label="Model wearing a red printed scarf" style="background:linear-gradient(#e8ece6,#b02a30 55%,#222)"></div>
    </div>
    <div class="promo-copy">
      <h2>ALL WESTERN</h2>
      <p>SLEEK &amp; SEXY</p>
      <div class="promo-figure">30<sup>%<small>OFF</small></sup></div>
    </div>
  </section>

  <footer class="site-footer">
    <div class="foot-col" style="left:28px"><h3><i></i>Shop</h3><ul><li>Upcoming Sales</li><li>Sales Ending Soon</li><li>Clothes Out</li><li>Accessories</li></ul></div>
    <div class="foot-col" style="left:230px"><h3><i></i>Action &amp; Info</h3><ul><li>About Us</li><li>Press</li><li>Our Partners</li><li>Gift Certificates</li></ul></div>
    <div class="foot-col" style="left:422px"><h3><i></i>Customer Care</h3><ul><li>Help / Customer Support</li><li>Return Policy</li><li>Shipping</li><li>FAQs</li></ul></div>
    <div class="social"><hr><span style="background:#24418a"></span><span style="background:#2aa9e0"></span><span style="background:#b4553c"></span><span style="background:#3a5270"></span><span style="background:#c91d24"></span><hr></div>
    <div class="news-title">NEWSLETTER SIGNUP</div>
    <div class="news-text">Preview sales, deals, news, updates, and more</div>
    <div class="news-form"><div class="news-input">Enter your email address...</div>
      <div class="news-btn"><svg width="22" height="16" viewBox="0 0 22 16" aria-hidden="true"><rect x="1" y="1" width="20" height="14" fill="#ccc"/><path d="M1 1l10 8 10-8" fill="none" stroke="#5b3f78" stroke-width="1.5"/></svg></div>
    </div>
    <div class="foot-bar"><span class="copy">© 2013 Sew To Suit | LLC. All Rights Reserved.</span><span class="legal">Terms of us &nbsp;•&nbsp; Privacy Policy &nbsp;•&nbsp; Contact</span></div>
  </footer>
</main>
</body>
</html>
```